Business Card for a mobile physiotherapy company

I need a layout for a business card for a mobile physiotherapy company.
Slogan is "Mobile Physiotherapy - Your Road To Recovery"
Phone number is 867-555-0142
Email VardenTherapy@postnest.ca (subject to change with website)
Website www.VardenTherapy.ca
My name and credentials: Luke Varden Luke Varden, BSc(kin), MPT, CAFCI, IMS
Information maybe included: Direct Billing, Services including Physiotherapy, IMS, acupuncture
Maybe include facebook and instagram logos
One side with the logo clean and sharp
Other side with details, try not to look too busy, keep everything concise

```html
<!DOCTYPE html>
<html lang="en">
<head>
<meta charset="utf-8">
<title>Varden Therapy – Business Card</title>
<link rel="stylesheet" href="https://fonts.googleapis.com/css2?family=Libre+Baskerville:wght@700&family=Open+Sans:wght@400;600&display=swap">
<style>
  :root {
    --stage: #1d1d1f;
    --navy: #2c4a75;
    --forest: #0d5446;
    --paper: #ffffff;
    --ink: #1f2a44;
  }
  * { box-sizing: border-box; margin: 0; padding: 0; }
  html, body { width: 1200px; height: 960px; overflow: hidden; background: var(--stage); }
  .canvas { position: relative; width: 1200px; height: 960px; }

  .card { position: absolute; width: 620px; height: 354px; overflow: hidden; border-radius: 4px; }

  /* Logo side */
  .card--logo { left: 520px; top: 90px; background: var(--navy); }
  .brand-name--front {
    position: absolute; left: 0; right: 0; top: 150px;
    text-align: center;
    font-family: "Open Sans", Arial, sans-serif; font-weight: 600;
    font-size: 46px; line-height: 1; color: var(--paper);
  }

  /* Details side */
  .card--details { left: 80px; top: 520px; background: var(--paper); }
  .details-panel { position: absolute; left: 0; top: 150px; width: 440px; height: 182px; background: var(--navy); border-bottom-right-radius: 26px; }
  .details-accent { position: absolute; left: 456px; top: 262px; width: 164px; height: 92px; background: var(--forest); border-top-left-radius: 20px; }

  .brand-name--back {
    position: absolute; left: 32px; top: 40px;
    font-family: "Open Sans", Arial, sans-serif; font-weight: 600;
    font-size: 32px; line-height: 1; color: var(--navy);
  }

  .tagline {
    position: absolute; left: 32px; top: 124px;
    font-family: "Libre Baskerville", Georgia, serif; font-weight: 700; font-size: 13px; color: var(--navy);
  }

  .person { position: absolute; right: 32px; top: 96px; text-align: right; color: var(--navy); }
  .person__name { font-family: "Libre Baskerville", Georgia, serif; font-weight: 700; font-size: 20px; letter-spacing: 1px; text-transform: uppercase; }
  .person__creds { font-family: "Open Sans", Arial, sans-serif; font-size: 11px; color: var(--ink); margin-top: 3px; }

  .contact-list { position: absolute; left: 32px; top: 172px; list-style: none; font-family: "Open Sans", Arial, sans-serif; font-size: 14px; color: var(--paper); }
  .contact-list li { display: flex; align-items: center; gap: 8px; height: 26px; }
  .contact-list svg { width: 15px; height: 15px; flex: none; }
  .services { position: absolute; left: 32px; top: 290px; font-family: "Open Sans", Arial, sans-serif; font-size: 13px; color: var(--paper); }
</style>
</head>
<body>
<main class="canvas">

  <section class="card card--logo" aria-label="Card logo side">
    <p class="brand-name brand-name--front">Varden Therapy</p>
  </section>

  <section class="card card--details" aria-label="Card details side">
    <div class="details-panel"></div>
    <div class="details-accent"></div>

    <p class="brand-name brand-name--back">Varden Therapy</p>

    <p class="tagline">Mobile Physiotherapy - Your Road To Recovery</p>

    <div class="person">
      <p class="person__name">Luke Varden</p>
      <p class="person__creds">BSc(kin), MPT, CAFCI, IMS</p>
    </div>

    <ul class="contact-list">
      <li>
        <svg viewBox="0 0 16 16" aria-hidden="true"><circle cx="8" cy="8" r="7" fill="none" stroke="#fff" stroke-width="1.2"/><path d="M5.5 4.5l1.5 0 .6 1.8-1 .8a5 5 0 0 0 2.3 2.3l.8-1 1.8.6 0 1.5c-3.5.3-6.3-2.5-6-6z" fill="#fff"/></svg>
        867-555-0142
      </li>
      <li>
        <svg viewBox="0 0 16 16" aria-hidden="true"><circle cx="8" cy="8" r="7" fill="none" stroke="#fff" stroke-width="1.2"/><rect x="4.3" y="5.3" width="7.4" height="5.4" fill="none" stroke="#fff" stroke-width="1"/><path d="M4.3 5.5L8 8.4l3.7-2.9" fill="none" stroke="#fff" stroke-width="1"/></svg>
        VardenTherapy@postnest.ca
      </li>
      <li>
        <svg viewBox="0 0 16 16" aria-hidden="true"><circle cx="8" cy="8" r="7" fill="none" stroke="#fff" stroke-width="1.2"/><ellipse cx="8" cy="8" rx="3" ry="7" fill="none" stroke="#fff" stroke-width="1"/><path d="M1 8h14" stroke="#fff" stroke-width="1"/></svg>
        www.VardenTherapy.ca
      </li>
    </ul>

    <p class="services">Direct Billing, Services Including Physiotherapy, Ims, Acupuncture</p>
  </section>

</main>
</body>
</html>
```